Redesign business cards

We have a new logo and I am not that happy with the layout of our existing card and looking for a change. Font is a bit small and the green can be hard to read. Logo may need a tidy up as the copy I have is not that hi-res too so require you to produce a hi-res version of the logo for us too. There will be three individual business cards to produce with just the names and phone numbers being different. Address will change too, but use what you see on the card for now.

Industry/Entity Type

Business

Requirements
Nice to have
• You could consider a redesign to the new logo, just not too radical. We like the blue and green hexagons as we feel that they are representative of oil industry that we are in.

```html
<!DOCTYPE html>
<html lang="en">
<head>
<meta charset="utf-8">
<title>NovaLube Oil Services – Business Card</title>
<link rel="stylesheet" href="https://fonts.googleapis.com/css2?family=Open+Sans:wght@400;600;700&display=swap">
<style>
  :root {
    --bg: #e9e7e3;
    --card: #ffffff;
    --green: #8dc63f;
    --blue: #1fa9e1;
    --orange: #f7941d;
    --ink: #3d3d3d;
    --white: #ffffff;
  }
  * { box-sizing: border-box; margin: 0; padding: 0; }
  html, body {
    width: 1200px; height: 829px; overflow: hidden;
    background: var(--bg);
    font-family: "Open Sans", Arial, sans-serif;
  }
  .canvas {
    position: relative; width: 1200px; height: 829px;
    display: flex; align-items: center; justify-content: center; gap: 60px;
  }
  .card {
    position: relative; width: 520px; height: 297px;
    background: var(--card); overflow: hidden;
    box-shadow: 0 6px 18px rgba(0,0,0,0.18);
  }
  .card-front .swoosh { position: absolute; inset: 0; }
  .brand {
    position: absolute; left: 38px; top: 60px;
    color: var(--green); font-weight: 700; font-size: 40px; line-height: 1;
    display: flex; align-items: center; gap: 10px;
  }
  .brand-sub { display: block; font-size: 18px; margin-top: 4px; }
  .brand-dot { width: 14px; height: 14px; background: var(--blue); border-radius: 50%; }
  .person { position: absolute; left: 38px; top: 150px; }
  .person-name { color: var(--orange); font-weight: 700; font-size: 17px; }
  .person-role { color: var(--blue); font-weight: 600; font-size: 14px; margin-top: 4px; }
  .address {
    position: absolute; left: 38px; top: 212px;
    color: var(--ink); font-size: 12.5px; line-height: 1.55;
  }
  .contact {
    position: absolute; right: 24px; top: 30px;
    list-style: none; color: var(--white); font-size: 12px; line-height: 1.9;
  }
  .contact li { display: flex; align-items: center; gap: 7px; }
  .contact svg { width: 11px; height: 11px; flex: none; }
  .card-back { background: var(--green); }
  .back-brand {
    position: absolute; left: 0; right: 0; top: 100px;
    display: flex; justify-content: center; align-items: center; gap: 12px;
    color: var(--white); font-weight: 700; font-size: 34px;
  }
  .back-dot { width: 16px; height: 16px; background: var(--white); border-radius: 50%; }
  .back-web {
    position: absolute; right: 40px; bottom: 52px;
    color: var(--white); font-size: 14px; letter-spacing: 3px;
  }
</style>
</head>
<body>
<main class="canvas">
  <section class="card card-front" aria-label="Card front">
    <svg class="swoosh" viewBox="0 0 520 297" width="520" height="297" aria-hidden="true">
      <path d="M300,0 C375,70 330,210 230,297 L520,297 L520,0 Z" fill="var(--green)"/>
      <path d="M322,0 C400,70 360,210 262,297 L520,297 L520,0 Z" fill="var(--blue)"/>
    </svg>
    <div class="brand">
      <div>NovaLube<span class="brand-sub">Oil Services</span></div>
      <span class="brand-dot"></span>
    </div>
    <div class="person">
      <p class="person-name">Daniel Harrow NZCE (Mech) P&amp;P</p>
      <p class="person-role">Director</p>
    </div>
    <p class="address">NovaLube Oil Services 41 Harbour Road<br>PO Box 1190 | Eastbrook<br>Queensland 4000</p>
    <ul class="contact">
      <li><svg viewBox="0 0 12 12"><path d="M3 1 L5 3.5 L4 4.8 Q5.2 7 7.2 8 L8.5 7 L11 9 L9.8 11 Q4 10.5 1 3 Z" fill="var(--white)"/></svg>+61 400 555 018</li>
      <li><svg viewBox="0 0 12 12"><rect x="1" y="2.5" width="10" height="7" fill="none" stroke="var(--white)" stroke-width="1.2"/><path d="M1 2.5 L6 6.5 L11 2.5" fill="none" stroke="var(--white)" stroke-width="1.2"/></svg>daniel@novalube.co.nz</li>
      <li><svg viewBox="0 0 12 12"><circle cx="6" cy="6" r="5" fill="none" stroke="var(--white)" stroke-width="1.2"/><ellipse cx="6" cy="6" rx="2.2" ry="5" fill="none" stroke="var(--white)" stroke-width="1"/><line x1="1" y1="6" x2="11" y2="6" stroke="var(--white)" stroke-width="1"/></svg>www.novalube.com.au</li>
    </ul>
  </section>

  <section class="card card-back" aria-label="Card back">
    <div class="back-brand"><span class="back-dot"></span>NovaLube</div>
    <p class="back-web">www.novalube.com.au</p>
  </section>
</main>
</body>
</html>
```